Pageforge Design Project

Utilising the PAGEFORGE Open source software, make changes to the current site to reflect current business and marketing plan.

This includes the actual structure and layout- less words and more images (not sure what). Also to provide link to most appropriate blog which would incorporate all my posts on Brank
Out, which is the main focus of my "commentary" on various topics given that I am a B to B operation. Review my current blog- "thoughts"- maybe get rid of it.

I have a Chatterbox fan page and Chirpline site and the site already has links to those, but I really don't utilise them much. You will not that I have top SEO ranking on seekora, both the business name and my name.

Go to http://www.tjartfulventures.example

Thanks

Dorian Halvorsen

Hi there

Having reviewed all submissions there is one key issue- stock business images. While I recognise I am a business, I have tried to differentiate myself from other businesses by showing myself as a bit more "arty". 

Lots of images of happy business people is not my style.

In most submissions the structure and function looks good through.

Thanks

Dorian

                                

From a colleague of mine:                                    

my overall impression is that it is all very corporate...perfect white teeth, squeaky clean and

far too many ties. Having worked in the arts for over 20 years none of the concepts is really reflective of the reality of working in the arts. Quirky, cutting edge, sophisticated in unique ways rather

than clichéd ways, beautiful, inspiring challenging...etc

Thanks

Dorian

I imagine gorgeous uplifting images from across

arts disciplines images, kids doing creative things, street art, gorgeous

dancers in mid flight, great public art, community, collaboration and maybe one

or two ties! Does this help?

 

F

                                       

All current designs are too corporate.

I sell business solutions to organisations that are engaged with the development and production of creative goods and services. Art, Theatre, Dance, Architecture, Community Festivals, Events, Creative Innovation Hubs.

I also help build bridges between the creative sector and business- for businesses who want create affiliations with arts to enhance their business and for the creative sector to receive in return goods and services or for joint venture purposes.

The site needs to show artistic flair, design sensibility and business acumen and strength. Some of these designs are on the right track

http://www.vistaglimmer.example/article/50-best-creative-websites-of-2011/4144/

Many thanks

Dorian

                                       

I have made some updates to my current site which better reflect what I am on about. now. There are some important key words there now

http://www.tjartfulventures.example

ow.                                   

                                       

ow.                                   

Target Market(s)

Business to Business but most customers will be educated and into cultural pursuits, theatre, opera, good food, wine, education

Industry/Entity Type

Marketing

Requirements
Must have
• Needs to show me as who I am- a bit different- think of Le Quart,
Nice to have
• Originality and appropriate links to social media
Blog
Should not have
• Sock standard business images

```html
<!DOCTYPE html>
<html lang="en">
<head>
<meta charset="utf-8">
<title>TJ Artful Ventures</title>
<link href="https://fonts.googleapis.com/css2?family=Yanone+Kaffeesatz:wght@500;700&family=PT+Sans+Narrow:wght@400;700&family=Open+Sans:wght@300;400;600&display=swap" rel="stylesheet">
<style>
:root{
  --orange:#f7931e;
  --ink:#2b2b2b;
  --text:#555;
  --nav:#2c2c2c;
  --hero-top:#1b1b1b;
  --hero-bottom:#3c3c3c;
  --footer:#ebebeb;
  --bar:#3a3a3a;
  --rule:#cfcfcf;
}
*{margin:0;padding:0;box-sizing:border-box}
html,body{width:777px;height:1200px;overflow:hidden;background:#fff}
body{position:relative;font-family:"Open Sans",sans-serif;color:var(--text)}
.abs{position:absolute}
.header{top:0;left:0;width:777px;height:86px;background:#fff}
.brand{left:46px;top:28px;display:flex;align-items:center;gap:8px}
.brand-square{width:18px;height:18px;background:var(--ink)}
.brand-name{font-family:"Open Sans",sans-serif;font-weight:400;font-size:19px;color:var(--ink);letter-spacing:.2px}
.search{left:548px;top:51px;width:181px;height:24px;border:1px solid #ddd;background:#fff}
.search span{position:absolute;left:9px;top:5px;font-size:8px;font-style:italic;color:#999}
.search svg{position:absolute;right:8px;top:5px}
.nav{top:86px;left:0;width:777px;height:39px;background:var(--nav);display:flex;padding-left:31px}
.nav a{font-family:"Yanone Kaffeesatz",sans-serif;font-weight:700;font-size:12.5px;color:#fff;text-decoration:none;text-transform:uppercase;line-height:39px;padding:0 7px;border-right:1px solid #474747;letter-spacing:.2px}
.nav a:last-child{border-right:0}
.hero{top:125px;left:0;width:777px;height:284px;background:linear-gradient(180deg,var(--hero-top),#262626 70%,var(--hero-bottom))}
.hero h1{position:absolute;left:41px;top:42px;font-family:"Yanone Kaffeesatz",sans-serif;font-weight:700;line-height:1.1}
.hero h1 .lead{display:block;color:var(--orange);font-size:30px}
.hero h1 .main{display:block;color:#fff;font-size:36px}
.hero p{position:absolute;left:42px;top:115px;width:285px;font-size:9.2px;line-height:15px;color:#eee}
.hero .arrows{position:absolute;left:44px;top:180px}
.dots{position:absolute;left:47px;top:231px;display:flex;gap:3px}
.dots i{width:8px;height:8px;border-radius:50%;background:#777}
.dots i:first-child{background:#fff}
.hero-photo{position:absolute;left:362px;top:24px;width:363px;height:226px;background:#fff;padding:4px;transform:rotate(-.8deg)}
.hero-photo div{width:100%;height:100%;background:linear-gradient(135deg,#e8dccf,#a9b4bf 55%,#6f7f8e)}
.col{width:216px}
.col h2{font-family:"PT Sans Narrow",sans-serif;font-weight:700;font-size:18px;color:var(--orange);margin-bottom:6px}
.col .pic{width:216px;height:100px}
.col p{margin-top:11px;font-size:8.3px;line-height:15.2px;color:#666;text-align:justify}
.more{display:inline-block;margin-top:5px;font-family:"PT Sans Narrow",sans-serif;font-weight:700;font-size:10px;color:#333;text-transform:uppercase;text-decoration:none}
.more::after{content:"";display:inline-block;margin-left:3px;border-left:4px solid #333;border-top:3px solid transparent;border-bottom:3px solid transparent}
.divider{top:680px;left:40px;width:700px;height:20px;background:radial-gradient(ellipse at 50% 0,rgba(0,0,0,.07),transparent 70%)}
.about h2{position:absolute;left:40px;top:706px;font-family:"Open Sans",sans-serif;font-weight:400;font-size:18.5px;color:#222;white-space:nowrap}
.about .pic{position:absolute;left:40px;top:747px;width:217px;height:153px;background:linear-gradient(90deg,#f4f4f4,#dfe3e8 55%,#4a4f58)}
.about .copy{position:absolute;left:276px;top:748px;width:444px;font-size:8.8px;line-height:15.2px;color:#555;text-align:justify}
.about .copy p+p{margin-top:20px}
.footer{top:948px;left:0;width:777px;height:215px;background:var(--footer)}
.footer h3{position:absolute;font-family:"PT Sans Narrow",sans-serif;font-weight:700;font-size:13px;color:#333;text-transform:uppercase}
.links{position:absolute;list-style:none}
.links li{font-size:9.2px;line-height:18.6px;color:#444}
.vrule{position:absolute;top:32px;width:1px;height:120px;background:var(--rule)}
.sub-note{position:absolute;left:313px;top:53px;font-size:9px;color:#444}
.email{position:absolute;left:311px;top:72px;width:186px;height:24px;background:#fff;border:1px solid #d6d6d6;border-radius:3px}
.email span{position:absolute;left:8px;top:6px;font-size:7.8px;font-style:italic;color:#aaa}
.subscribe{position:absolute;left:435px;top:101px;width:61px;height:18px;background:var(--orange);border-radius:2px;color:#fff;font-family:"PT Sans Narrow",sans-serif;font-weight:700;font-size:8.5px;text-align:center;line-height:18px;text-transform:uppercase}
.social{position:absolute;left:560px;top:53px;list-style:none}
.social li{display:flex;align-items:center;gap:6px;font-size:9px;line-height:14px;color:#222}
.social li::before{content:"";width:9px;height:9px;border-radius:50%;background:#111}
.foot-brand{position:absolute;left:561px;top:112px;display:flex;align-items:center;gap:8px}
.foot-brand .brand-square{background:#999}
.foot-brand .brand-name{color:#999;font-size:18px}
.bar{top:1163px;left:0;width:777px;height:37px;background:var(--bar)}
.bar p{position:absolute;left:52px;top:14px;font-size:7.5px;color:#ccc}
</style>
</head>
<body>

<header class="abs header">
  <div class="abs brand"><span class="brand-square"></span><span class="brand-name">tj artful ventures</span></div>
  <div class="abs search"><span>Search here..</span>
    <svg width="13" height="13" viewBox="0 0 13 13"><circle cx="5.5" cy="5.5" r="4" fill="none" stroke="#888" stroke-width="2"/><line x1="8.5" y1="8.5" x2="12" y2="12" stroke="#888" stroke-width="2.4" stroke-linecap="round"/></svg>
  </div>
</header>

<nav class="abs nav">
  <a href="#">Home</a><a href="#">Helping you plan</a><a href="#">Crative Strategy</a><a href="#">Implementing your plans</a><a href="#">Workshops</a><a href="#">Projects</a><a href="#">Our Team</a><a href="#">Clients</a><a href="#">Our Thoughts</a><a href="#">Cotnact us</a>
</nav>

<section class="abs hero">
  <h1><span class="lead">Innovation, Enterprise</span><span class="main">and Creative Strategy</span></h1>
  <p>TJ Artful Ventures is a business consultancy dedicated to helping businesses within the arts, cultural and creative industries develop the business tools they need to achieve their creative vision.</p>
  <svg class="arrows" width="40" height="22" viewBox="0 0 40 22"><polyline points="10,2 2,11 10,20" fill="none" stroke="#fff" stroke-width="1.8"/><polyline points="26,2 34,11 26,20" fill="none" stroke="#fff" stroke-width="1.8"/></svg>
  <div class="dots"><i></i><i></i><i></i><i></i></div>
  <div class="hero-photo"><div role="img" aria-label="Slideshow photo: a group of smiling colleagues in business attire"></div></div>
</section>

<article class="abs col" style="left:40px;top:433px">
  <h2>Creative Organisations</h2>
  <div class="pic" role="img" aria-label="Photo: team meeting in a bright office" style="background:linear-gradient(90deg,#c9d6e2,#e9eef2 45%,#9fb4c6)"></div>
  <p>Are you a not for profit arts organisation looking for long-term stability and success, creatively and financially? We can assist by keeping your objectives and financial viability in balance. We'll help you adopt strong business</p>
  <a class="more" href="#">Learn more</a>
</article>

<article class="abs col" style="left:280px;top:433px">
  <h2>Creative Business</h2>
  <div class="pic" role="img" aria-label="Photo: a giant light bulb in a green field under a blue sky" style="background:linear-gradient(180deg,#2f6f9e,#9fc6dc 55%,#7fa24a 80%,#4f6f2a)"></div>
  <p>Are you a new or growing creative business that needs help with your direction? We can show you how to adopt world's best practice principles and support the develop-ment of your creative</p>
  <a class="more" href="#">Learn more</a>
</article>

<article class="abs col" style="left:520px;top:433px">
  <h2>Creative Communities</h2>
  <div class="pic" role="img" aria-label="Photo: a group joining hands in a circle against the sky" style="background:linear-gradient(180deg,#cfe4f3,#6f9fc9 60%,#3f6f99)"></div>
  <p>Are you a creative community that needs direction to help you get creative projects off the ground? We work with community groups and local Councils to assist in the development</p>
  <a class="more" href="#">Learn more</a>
</article>

<div class="abs divider"></div>

<section class="about">
  <h2>How to Maximise the Potential of your Organisation</h2>
  <div class="pic" role="img" aria-label="Photo: a businessman drawing a rising red growth line"></div>
  <div class="copy">
    <p>TJ Artful Ventures is a business consultancy dedicated to helping businesses within the arts, cultural and creative industries develop the business tools they need to achieve their creative vision. We also work with communities at at local government level, supporting the development of policy in relation to events, festivals and public art programs.</p>
    <p>Another component of our business is to support other businesses seeking an alignment with arts projects as part of their company's marketing objectives. To this end TJ Artful Ventures has worked with CBAN (Civic Business Arts Network) now Creative Alliances Collective on developing partnership proposals with compa-nies wanting brand alignment with arts companies.</p>
  </div>
</section>

<footer class="abs footer">
  <h3 style="left:54px;top:26px">Company</h3>
  <ul class="links" style="left:54px;top:47px"><li>Home</li><li>Helping you Plan</li><li>Creative Strategy</li><li>Implementing your plans</li><li>Workshops</li><li>Projects</li></ul>
  <ul class="links" style="left:187px;top:50px"><li>Our Team</li><li>Clients</li><li>Our Thoughts</li><li>Contact Us</li></ul>
  <div class="vrule" style="left:275px"></div>
  <h3 style="left:311px;top:26px">Subscribe Newsletter</h3>
  <p class="sub-note">Please sign up here for latest newsletters</p>
  <div class="email"><span>email address</span></div>
  <div class="subscribe">Subscribe</div>
  <div class="vrule" style="left:530px"></div>
  <h3 style="left:560px;top:26px">Get in touch with us</h3>
  <ul class="social"><li>Chatterbox</li><li>Chirpline</li><li>Brank Out</li></ul>
  <div class="foot-brand"><span class="brand-square"></span><span class="brand-name">tj artful ventures</span></div>
</footer>

<div class="abs bar"><p>© 2013 Company Name. All right reserved. Term of Use</p></div>

</body>
</html>
```